Garland Custom Boats Website update

I would like an updated website to my current site (Garlandboats.com).
I have an updated logo i would like to incorporate.
24 pages , would like to integrate videos of the boats (that i can upload later)

Target Market(s)

Professional and Commercial boat owners

Industry/Entity Type

Custom Boat Manufacturing

Coding

Coded - Design and coding required

Number of Pages Required

5+ page

Font styles to use
Serif

Requirements
Must have
• Easy to read, well laid-out, and video integration
Nice to have
• Fresh up to date look

```html
<!DOCTYPE html>
<html lang="en">
<head>
<meta charset="utf-8">
<title>Garland Custom Boats</title>
<link rel="stylesheet" href="https://fonts.googleapis.com/css2?family=Poppins:wght@400;500;600;700;800&family=Roboto:wght@400;500;700;900&display=swap">
<style>
:root{
  --ocean-deep:#0d3a86;
  --ocean-mid:#1f66b8;
  --ocean-light:#2fa7d6;
  --brand-blue:#0b43a6;
  --band-blue:#1a47a6;
  --brand-red:#d0242e;
  --ink:#111111;
  --text:#222222;
  --white:#ffffff;
  --footer:#000000;
}
*{box-sizing:border-box;margin:0;padding:0}
html,body{width:1200px;height:3857px;overflow:hidden;background:var(--white)}
body{position:relative;font-family:"Poppins",sans-serif;color:var(--text)}
.abs{position:absolute}

/* Hero */
.hero{left:0;top:0;width:1200px;height:737px;
  background:radial-gradient(ellipse at 15% 40%,var(--ocean-light) 0%,var(--ocean-mid) 25%,var(--ocean-deep) 60%,#0a2f70 100%)}
.menu-toggle{left:1042px;top:28px;width:38px;height:24px}
.menu-toggle span{display:block;height:2px;background:var(--white);margin-bottom:8px}
.menu-toggle span:nth-child(3){width:26px;margin-left:12px}
.hero-brand{left:300px;top:205px;width:600px;text-align:center;color:var(--white);
  font-family:"Roboto",sans-serif;font-weight:900;line-height:1}
.hero-brand .name{font-size:84px;letter-spacing:2px}
.hero-brand .sub{font-size:32px;letter-spacing:6px;margin-top:14px}
.follow-label{left:1137px;top:218px;color:var(--white);font-size:10px;writing-mode:vertical-rl}
.social{left:1135px;width:14px;height:14px;border-radius:50%;background:var(--white)}
.social-main{left:1122px;top:288px;width:42px;height:42px}
.follow-line{left:1140px;top:445px;width:1px;height:142px;background:rgba(255,255,255,.7)}
.slide-dot{left:80px;width:6px;height:6px;border-radius:50%;background:var(--white)}
.slide-dot.active{width:10px;height:10px;left:78px;background:none;border:2px solid var(--white)}

/* About */
.photo{border-radius:26px}
.about-main{left:138px;top:842px;width:318px;height:463px;background:linear-gradient(180deg,#c9d3dc 0%,#aab8c6 55%,#6f8497 100%)}
.about-top{left:471px;top:895px;width:186px;height:170px;background:linear-gradient(180deg,#7eb4d9 0%,#2d85b8 100%)}
.about-bottom{left:391px;top:1091px;width:187px;height:170px;background:linear-gradient(180deg,#2b3e4c 0%,#8b8c90 55%,#4b5866 100%)}
.about-title{left:697px;top:865px;width:400px;font-family:"Roboto",sans-serif;font-weight:900;
  font-size:38px;line-height:46px;color:var(--brand-blue);letter-spacing:.5px}
.swoosh{left:697px;top:955px;width:266px;height:14px}
.about-text{left:699px;top:984px;width:370px;font-size:13px;line-height:19.4px;color:var(--text);font-family:"Roboto",sans-serif}
.yacht-photo{left:640px;top:1195px;width:560px;height:220px;
  background:linear-gradient(90deg,rgba(255,255,255,1) 0%,rgba(214,233,246,.8) 30%,#a9cde6 70%,#8ab7da 100%)}
.btn-book{left:692px;top:1224px;width:165px;height:50px;border-radius:25px;background:var(--brand-red);
  color:var(--white);font-weight:600;font-size:13px;display:flex;align-items:center;padding-left:25px;gap:14px}
.btn-book i{width:28px;height:28px;border-radius:50%;background:var(--white);display:flex;align-items:center;justify-content:center}

/* Video */
.video{left:0;top:1415px;width:1200px;height:655px;
  background:linear-gradient(180deg,#5d6670 0%,#8a8177 40%,#4a5865 70%,#24394f 100%)}
.video-shade{left:0;top:1415px;width:1200px;height:655px;background:rgba(20,30,45,.35)}
.play{left:554px;top:1652px;width:92px;height:92px;border-radius:50%;border:2px solid var(--white);
  display:flex;align-items:center;justify-content:center}
.video-label{left:0;top:1775px;width:1185px;text-align:center;color:var(--white);font-weight:700;font-size:42px;font-family:"Roboto",sans-serif}

/* Section titles */
.section-title{left:0;width:1200px;text-align:center;font-family:"Roboto",sans-serif;font-weight:700;font-size:42px}
.title-line{left:466px;width:268px;height:10px}

/* Services */
.service-photo{border-radius:14px}
.service-label{height:48px;background:var(--brand-red);color:var(--white);font-family:"Roboto",sans-serif;
  font-weight:500;font-size:21px;display:flex;align-items:center;justify-content:center;white-space:nowrap}
.s1{left:138px;top:2232px;width:286px;height:286px;background:linear-gradient(180deg,#8fb26b 0%,#dfe6ea 45%,#6d98b8 100%)}
.s2{left:458px;top:2265px;width:286px;height:285px;background:linear-gradient(180deg,#6d8bab 0%,#d8dde2 50%,#4f7da6 100%)}
.s3{left:774px;top:2232px;width:286px;height:286px;background:linear-gradient(180deg,#8cc0e8 0%,#e6eef2 35%,#4fb7b2 70%,#2c9a9c 100%)}
.l1{left:162px;top:2518px;width:237px}
.l2{left:481px;top:2550px;width:238px;box-shadow:0 8px 10px rgba(0,0,0,.2)}
.l3{left:800px;top:2518px;width:237px}
.s2-arrow{left:578px;top:2388px;width:44px;height:44px;border-radius:50%;background:rgba(255,255,255,.85);display:flex;align-items:center;justify-content:center}
.chev{width:24px;height:32px}

/* Testimonials */
.testimonials{left:0;top:2692px;width:1200px;height:551px;background:linear-gradient(180deg,#1a47a6 0%,#1d4bb0 100%)}
.quote-card{background:var(--white);border-radius:6px;text-align:center;font-size:13px;line-height:19px;color:var(--text);padding:0 26px}
.quote-card .mark{font-family:"Roboto",sans-serif;font-weight:900;font-size:32px;line-height:32px;color:var(--ink);margin:22px 0 6px}
.q1{left:144px;top:2927px;width:256px;height:191px}
.q2{left:447px;top:2909px;width:305px;height:228px}
.q3{left:801px;top:2927px;width:256px;height:191px}

/* Partners */
.partner{top:3333px;width:170px;height:127px;border:2px solid var(--brand-blue);border-radius:12px;display:flex;align-items:center;justify-content:center}
.badge{background:#c9ced8}

/* Footer */
.footer{left:0;top:3558px;width:1200px;height:299px;background:var(--footer)}
.footer-brand{left:0;top:3618px;width:1200px;text-align:center;font-family:"Roboto",sans-serif;font-weight:900;color:var(--brand-blue);line-height:1}
.footer-brand .name{font-size:54px;letter-spacing:2px}
.footer-brand .sub{font-size:20px;letter-spacing:4px;margin-top:6px}
.footer-nav{left:0;top:3734px;width:1200px;display:flex;justify-content:center;gap:36px;font-family:"Roboto",sans-serif;font-size:16px;color:var(--white);list-style:none}
.footer-nav .current{color:var(--brand-red)}
.copyright{left:0;top:3780px;width:1200px;text-align:center;color:var(--white);font-size:13px}
</style>
</head>
<body>

<!-- Hero -->
<section class="abs hero" role="img" aria-label="Aerial view of a speedboat cutting a white wake through deep blue water"></section>
<div class="abs menu-toggle"><span></span><span></span><span></span></div>
<div class="abs hero-brand"><div class="name">GARLAND</div><div class="sub">CUSTOM BOATS</div></div>
<div class="abs follow-label">Follow us</div>
<div class="abs social social-main" aria-label="Social link"></div>
<div class="abs social" style="top:340px" aria-label="Social link"></div>
<div class="abs social" style="top:379px" aria-label="Social link"></div>
<div class="abs social" style="top:418px" aria-label="Social link"></div>
<div class="abs follow-line"></div>
<div class="abs slide-dot active" style="top:379px"></div>
<div class="abs slide-dot" style="top:403px"></div>
<div class="abs slide-dot" style="top:427px"></div>
<div class="abs slide-dot" style="top:448px"></div>

<!-- About -->
<div class="abs photo about-main" role="img" aria-label="Custom sport fishing boat running on calm water"></div>
<div class="abs photo about-top" role="img" aria-label="Dive boat moored in turquoise water"></div>
<div class="abs photo about-bottom" role="img" aria-label="Boats at anchor at sunset under tree branches"></div>
<h1 class="abs about-title">GARLAND CUSTOM BOATS</h1>
<svg class="abs swoosh" viewBox="0 0 266 14"><path d="M0 9 Q130 0 266 6 Q130 6 0 12Z" fill="#d0242e"/></svg>
<p class="abs about-text">is a premier manufacturer of custom boats, specializing in the creation of high-quality vessels ranging from 28 to 72 feet in length. With a strong focus on precision and craftsmanship, we design and build boats tailored to meet the diverse needs of our clients. Our portfolio spans a wide array of markets, featuring everything from sleek recreational fishing boats, ready for adventures on the water, to robust commercial diving vessels designed to thrive in the toughest conditions. Regardless of the purpose, each boat is a testament to our commitment to excellence and innovation in marine design.</p>
<div class="abs yacht-photo" role="img" aria-label="White luxury yacht cruising on open water"></div>
<a class="abs btn-book">BOOK NOW <i><svg width="14" height="14" viewBox="0 0 14 14"><path d="M2 7H12M8 3L12 7L8 11" stroke="#d0242e" stroke-width="1.6" fill="none"/></svg></i></a>

<!-- Video -->
<section class="abs video" role="img" aria-label="Friends relaxing on the bow of a sailboat at sea"></section>
<div class="abs video-shade"></div>
<div class="abs play"><svg width="26" height="28" viewBox="0 0 26 28"><path d="M5 3L22 14L5 25Z" stroke="#fff" stroke-width="2" fill="none"/></svg></div>
<div class="abs video-label">Video</div>

<!-- Services -->
<h2 class="abs section-title" style="top:2148px;color:var(--ink)">Services</h2>
<svg class="abs title-line" style="top:2203px" viewBox="0 0 268 10"><path d="M0 5 Q134 0 268 5 Q134 10 0 5Z" fill="#d0242e"/></svg>
<svg class="abs chev" style="left:68px;top:2360px" viewBox="0 0 24 32"><path d="M17 5L7 16L17 27" stroke="#111" stroke-width="3.5" fill="none"/></svg>
<svg class="abs chev" style="left:1110px;top:2360px" viewBox="0 0 24 32"><path d="M7 5L17 16L7 27" stroke="#111" stroke-width="3.5" fill="none"/></svg>
<div class="abs service-photo s1" role="img" aria-label="42 foot reef boat under way"></div>
<div class="abs service-label l1">42' Reef Runner</div>
<div class="abs service-photo s2" role="img" aria-label="36 foot harbor patrol boat under way"></div>
<div class="abs s2-arrow"><svg width="18" height="14" viewBox="0 0 18 14"><path d="M1 7H16M11 2L16 7L11 12" stroke="#d0242e" stroke-width="1.6" fill="none"/></svg></div>
<div class="abs service-label l2">36' Harbor Patrol</div>
<div class="abs service-photo s3" role="img" aria-label="31 foot utility boat docked in turquoise water"></div>
<div class="abs service-label l3">31' Guardian</div>

<!-- Testimonials -->
<section class="abs testimonials" role="img" aria-label="Blue background with a coiled mooring rope"></section>
<h2 class="abs section-title" style="top:2762px;color:var(--white)">Testimonials</h2>
<svg class="abs title-line" style="top:2822px" viewBox="0 0 268 10"><path d="M0 5 Q134 0 268 5 Q134 10 0 5Z" fill="#d0242e"/></svg>
<svg class="abs chev" style="left:86px;top:2995px" viewBox="0 0 24 32"><path d="M17 5L7 16L17 27" stroke="#fff" stroke-width="3.5" fill="none"/></svg>
<svg class="abs chev" style="left:1088px;top:2995px" viewBox="0 0 24 32"><path d="M7 5L17 16L7 27" stroke="#fff" stroke-width="3.5" fill="none"/></svg>
<div class="abs quote-card q1"><div class="mark">&ldquo;&rdquo;</div>Lorem ipsum dolor sit amet, consectetur adipiscing elit, sed do eiusmod tempor incididunt ut labore et dolore magna aliqua. Quis ipsum suspendisse</div>
<div class="abs quote-card q2"><div class="mark">&ldquo;&rdquo;</div>Lorem ipsum dolor sit amet, consectetur adipiscing elit, sed do eiusmod tempor incididunt ut labore et dolore magna aliqua. Quis ipsum suspendisse ultrices gravida. Risus commodo viverra maecenas accumsan lacus vel facilisis.</div>
<div class="abs quote-card q3"><div class="mark">&ldquo;&rdquo;</div>Lorem ipsum dolor sit amet, consectetur adipiscing elit, sed do eiusmod tempor incididunt ut labore et dolore magna aliqua. Quis ipsum suspendisse</div>

<!-- Partners -->
<svg class="abs chev" style="left:99px;top:3382px" viewBox="0 0 24 32"><path d="M17 5L7 16L17 27" stroke="#111" stroke-width="3.5" fill="none"/></svg>
<svg class="abs chev" style="left:1070px;top:3382px" viewBox="0 0 24 32"><path d="M7 5L17 16L7 27" stroke="#111" stroke-width="3.5" fill="none"/></svg>
<div class="abs partner" style="left:152px"><div class="badge" style="width:80px;height:34px"></div></div>
<div class="abs partner" style="left:334px"><div class="badge" style="width:96px;height:96px;border-radius:50%"></div></div>
<div class="abs partner" style="left:515px"><div class="badge" style="width:140px;height:24px"></div></div>
<div class="abs partner" style="left:696px"><div class="badge" style="width:90px;height:110px;border-radius:45%"></div></div>
<div class="abs partner" style="left:877px"><div class="badge" style="width:96px;height:30px"></div></div>

<!-- Footer -->
<footer class="abs footer"></footer>
<div class="abs footer-brand"><div class="name">GARLAND</div><div class="sub">CUSTOM BOATS</div></div>
<ul class="abs footer-nav">
  <li class="current">Home</li><li>About Us</li><li>Boats</li><li>Services</li><li>Testimonials</li><li>Contact Us</li>
</ul>
<div class="abs copyright">© 2025 |www.garlandcustomboats.com</div>

</body>
</html>
```